Bench Advertisement - We Buy Houses Design Needed

Need a catchy, simple but elegant design for bus benches to advertise our company.

We need our website, or phone number, and a smal description (1-2 bulletpoints of what we do and what we offer)

The tricky part is for the designer to fit everything and make the website name as part of the title and fitting everything so that people passing by on the street can see what we offer.

Our website is quickdealhomebuyer.com - (916) 555-0143

Something simple but something that catches the eye of walking pedestrians, and drivers driving by the bench.

Our company buys houses, any condition, any situation, we buy houses for cash and close quickly. You can use this description to create a few bulletpoints however you like. Must follow dimensions in attachment.

Target Market(s)

People in foreclosure, about to lose their homes, people that need a quick cash sale of their property

Industry/Entity Type

Real Estate

Requirements
Must have
• catchy, website name, phone number, few brief bulletpoints about what we offer, colors that will catch peoples eye while walking or driving - advertisement will be placed on bus benches - visit our website to see the type of houses we buy - Also have more work for winner of design with possible bonuses
Nice to have
• Feel free to use description or images on our website - make sure the description is just bullet points and it fits with the overall theme / size of the advertisement - Bold bright colors - put yourself in their shoes (if you were going through financial difficulties and about to lose your house to foreclosure or auction, what would you want to see to pick up the phone and call us for a quick sale of your house?) (or if you have a house that you are having a problem with, problem renters, unkept/beat up house, what would make you want to call us and sell your house to us?)

```html
<!DOCTYPE html>
<html lang="en">
<head>
<meta charset="utf-8">
<title>Quick Deal Home Buyer – Bench Advertisement</title>
<link rel="stylesheet" href="https://fonts.googleapis.com/css2?family=Oswald:wght@300;400&family=Open+Sans:wght@400&display=swap">
<style>
  :root {
    --page-bg: #efebe7;
    --band-dark: #b4521f;
    --band-bottom: #a84a1c;
    --band-main: #e37a1f;
    --ink-light: #ffffff;
    --accent-dark: #9a4016;
  }
  * { box-sizing: border-box; margin: 0; padding: 0; }
  html, body {
    width: 1200px; height: 1061px; overflow: hidden;
    background: var(--page-bg);
  }
  .canvas {
    position: relative; width: 1200px; height: 1061px;
    display: flex; align-items: center; justify-content: center;
  }
  .bench-ad {
    width: 1120px; height: 520px;
    background: var(--band-dark);
    display: flex; flex-direction: column;
    box-shadow: 0 10px 30px rgba(0,0,0,0.18);
  }
  .headline-band {
    height: 125px;
    display: flex; align-items: center; justify-content: center;
    font-family: "Open Sans", sans-serif;
    font-size: 36px; color: var(--ink-light);
    letter-spacing: 0.2px;
  }
  .offer-band {
    height: 285px;
    background: var(--band-main);
    padding: 12px 14px;
  }
  .offer-frame {
    height: 100%;
    border: 2px solid rgba(255,255,255,0.9);
    display: flex; flex-direction: column; align-items: center; justify-content: center;
    font-family: "Oswald", sans-serif; color: var(--ink-light);
  }
  .brand-name {
    font-family: "Oswald", sans-serif; font-weight: 300;
    font-size: 14px; letter-spacing: 0.5px; text-transform: uppercase;
    color: var(--accent-dark);
    display: flex; align-items: center; gap: 6px;
    margin-bottom: 2px;
  }
  .brand-name .brand-dot {
    width: 9px; height: 9px; background: var(--accent-dark);
  }
  .website {
    font-weight: 400; font-size: 56px; line-height: 1.1;
  }
  .phone {
    display: flex; align-items: center; gap: 12px;
    font-weight: 300; font-size: 36px; color: var(--accent-dark);
    margin-bottom: 10px;
  }
  .offer-list { list-style: none; }
  .offer-list li {
    display: flex; align-items: center; justify-content: center; gap: 14px;
    font-weight: 300; font-size: 32px; line-height: 1.35;
  }
  .offer-list .chevron { width: 12px; height: 20px; }
  .footer-band { flex: 1; background: var(--band-bottom); }
</style>
</head>
<body>
<main class="canvas">
  <section class="bench-ad">
    <header class="headline-band">Just Look at on Orange Area</header>
    <div class="offer-band">
      <div class="offer-frame">
        <div class="brand-name"><span class="brand-dot"></span>Quick Deal Home Buyer</div>
        <div class="website">quickdealhomebuyer.com</div>
        <div class="phone">
          <svg width="30" height="30" viewBox="0 0 30 30" aria-hidden="true">
            <circle cx="15" cy="15" r="13" fill="none" stroke="#9a4016" stroke-width="2"/>
            <path d="M10.5 8.5c1-.8 2-.6 2.5.4l1 2c.4.8.2 1.5-.5 2l-.8.6c.6 1.6 1.9 3 3.6 3.7l.6-.8c.5-.7 1.3-.9 2-.5l2 1c1 .5 1.2 1.5.4 2.5-1.2 1.4-3 1.8-5 .8-3-1.5-5.3-3.8-6.6-6.8-.8-1.9-.5-3.7.8-4.9z" fill="#9a4016"/>
          </svg>
          <span>(916) 555-0143</span>
        </div>
        <ul class="offer-list">
          <li>
            <svg class="chevron" viewBox="0 0 12 20" aria-hidden="true"><path d="M0 0h5l7 10-7 10H0l7-10z" fill="#9a4016"/></svg>
            We buy houses for cash and close quickly
            <svg class="chevron" viewBox="0 0 12 20" aria-hidden="true"><path d="M12 0H7L0 10l7 10h5L5 10z" fill="#9a4016"/></svg>
          </li>
          <li>
            <svg class="chevron" viewBox="0 0 12 20" aria-hidden="true"><path d="M0 0h5l7 10-7 10H0l7-10z" fill="#9a4016"/></svg>
            Our company buys houses, any condition, any situation
            <svg class="chevron" viewBox="0 0 12 20" aria-hidden="true"><path d="M12 0H7L0 10l7 10h5L5 10z" fill="#9a4016"/></svg>
          </li>
        </ul>
      </div>
    </div>
    <div class="footer-band"></div>
  </section>
</main>
</body>
</html>
```